Dentistry Office

We want a new design for a Dentist's office website.

The theme is: "We provide high quality, state-of-the-art, dental care in a comfortable, caring environment."

The site currently has a menu on the left of the page with about 40 items on it. There is a great deal of textual content on each page, plus several illustrations.

We want to do this using CSS, so we need specifications in the CSS for all possible elements. The CSS needs to be named in a logical manner for easy use.

Every dentist on the planet seems to use lots of Flash. We don't want to because it is so distracting. We are looking for an elegant solution targeting 24-55 age group, but not excluding anyone.

The following (from another dentist's site) can give you a taste of what we want to communicate on the site:

"After 20 years of teaching dentists how to refine their technique and many years of writing textbooks, I currently devote my time to my office and the hands-on practice of dentistry. I'd like to welcome you personally to my dental practice, and I invite you to meet my highly experienced team of professionals.

"We have offered complete dental care of the highest quality since 1978. We provide Preventive Services, Tooth Whitening and Cosmetic Dentistry for a beautiful smile, Endodontics (root canal treatment) to treat painful teeth, Sedation Dentistry so you can relax, and Dental Implants to restore what is missing. We offer total care.

"Our approach to your health is simple: We use our education, experience and dedication to provide every patient with superior dental care.

"This passion for excellence is not just a goal, but a standard every member of our team holds.

"We also pride ourselves with our state of the art procedures, training and technology. This includes creating a beautiful smile using techniques that preserve as much of the original tooth as possible.

"Our abilities are renowned throughout the dental profession and I hope if you have any questions you will contact us by an e-mail note, by phone or just by dropping by."

Keep in mind the screen shape and dimensions. Your design needs to work in the normal screen proportions, regardless of how it looks when you post it here. Scrolling is OK, but the first impression needs to work.
Updates

Keep in mind that there will be about 250 words, or more, on each page.

Competitors web sites:

http://www.brindlecovedentist.example/

http://www.brindlecovedentalcare.example/

http://www.grinsbymarlowvaledental.example/

http://www.tenbyfamilydentalcare.example/

http://www.quelmardental.example/

http://www.dovrinadental.example/

We need to compete with these.

Target Market(s)

Generally adults seeking the most experienced and comfortable-to-be-with dentist.

Industry/Entity Type

Training

Requirements
Must have
• Must stand apart from other dentists.
• Must be elegant.
• Must have a horizontal menu structure across all columns, NOT a vertical that requires scrolling, no popout, pop down, etc. menus.
• We are looking for something special.
• Do not waste your time or ours putting up templates and things you have used before.
• Personally, I do not see how someone outside the US can understand the northern California dental market. But you are welcome to try.
Should not have
• Flash or graphics that move
• The look of a template
• Folksy fonts
• Looks like you used it 20 times before

```html
<!DOCTYPE html>
<html lang="en">
<head>
<meta charset="utf-8">
<title>Dentist's Office</title>
<link rel="stylesheet" href="https://fonts.googleapis.com/css2?family=Arimo:wght@400;700&family=Open+Sans:wght@400&family=Questrial&display=swap">
<style>
  :root {
    --frame-blue: #1a6697;
    --nav-blue: #14639a;
    --deep-blue: #195a89;
    --head-blue: #1b6aa0;
    --item-grey: #ececec;
    --item-line: #ffffff;
    --page-white: #ffffff;
    --text-grey: #5a5a5a;
    --soft-grey: #8a8a8a;
    --gold: #d3a14a;
    --active-grey: #e9e9e9;
  }
  * { box-sizing: border-box; margin: 0; padding: 0; }
  html, body { width: 1023px; height: 1200px; overflow: hidden; }
  body {
    position: relative;
    background: var(--frame-blue);
    font-family: "Arimo", Arial, sans-serif;
  }
  .page {
    position: absolute; left: 21px; top: 28px; width: 981px; height: 1130px;
    background: var(--page-white);
  }
  .brand {
    position: absolute; left: 62px; top: 36px; display: flex; align-items: center; gap: 12px;
  }
  .brand-mark { width: 40px; height: 40px; border-radius: 50%; background: #5fb9e0; }
  .brand-name { font-family: "Arimo", sans-serif; font-weight: 700; font-size: 24px; color: var(--deep-blue); }
  .call-us {
    position: absolute; right: 20px; top: 10px; font-size: 21px; font-weight: 700; color: var(--deep-blue);
  }
  .call-us span { color: #7d7d7d; }

  .side-menu { position: absolute; left: 2px; top: 104px; width: 205px; }
  .side-menu h3 {
    height: 18.7px; line-height: 18.7px; background: var(--head-blue); color: #fff;
    font-size: 14.5px; font-weight: 400; text-align: center;
  }
  .side-menu li {
    list-style: none; height: 18.7px; line-height: 18.7px; background: var(--item-grey);
    border-bottom: 1px solid var(--item-line); font-size: 12px; color: #222; padding-left: 16px;
    white-space: nowrap;
  }
  .divider { position: absolute; left: 210px; top: 104px; width: 2px; height: 1020px; background: #e6e6e6; }

  .side-box {
    position: absolute; left: 2px; width: 205px; border-radius: 8px; color: #fff;
    background: linear-gradient(#1f78b0, #135e93);
  }
  .side-box h4 { position: absolute; font-size: 15.5px; font-weight: 400; white-space: nowrap; }
  .side-box .line { position: absolute; font-size: 12px; white-space: nowrap; }
  .side-box .picture { position: absolute; border-radius: 3px; }
  .quick-contact { top: 809px; height: 146px; }
  .online-support { top: 972px; height: 146px; }

  .main-nav {
    position: absolute; left: 222px; top: 103px; width: 745px; height: 45px;
    background: var(--nav-blue); display: flex; align-items: stretch; border-radius: 2px;
  }
  .main-nav a {
    flex: none; white-space: nowrap;
    color: #fff; text-decoration: none; font-size: 16.5px; line-height: 45px; padding: 0 9px;
  }
  .main-nav a:first-child { padding-left: 11px; }
  .main-nav a.active { background: var(--active-grey); color: #222; margin: 0 10px 0 14px; padding: 0 7px; }

  .hero {
    position: absolute; left: 220px; top: 156px; width: 749px; height: 263px;
    border: 1px solid #e2e2e2; border-radius: 10px; overflow: hidden; background: #fff;
  }
  .hero-photo {
    position: absolute; right: 0; top: 0; width: 470px; height: 100%;
    background: linear-gradient(90deg, #ffffff 0%, #e9ddd2 25%, #caa58c 55%, #e6d3b8 80%, #f1ebe3 100%);
  }
  .hero-question { position: absolute; left: 9px; top: 53px; font-family: "Questrial", sans-serif; font-size: 18px; color: var(--gold); white-space: nowrap; }
  .hero-visit { position: absolute; left: 77px; top: 96px; font-family: "Questrial", sans-serif; font-size: 22px; color: #555; white-space: nowrap; }

  .welcome {
    position: absolute; left: 230px; top: 433px; width: 737px; height: 685px;
    border-radius: 16px; background: #fff;
    box-shadow: 0 0 6px rgba(0,0,0,0.12);
  }
  .welcome h1 {
    position: absolute; left: 16px; top: 28px; font-family: "Questrial", sans-serif; font-weight: 400; font-size: 31px; white-space: nowrap;
  }
  .welcome h1 strong { color: var(--deep-blue); font-family: "Arimo", sans-serif; font-weight: 700; font-size: 29px; }
  .welcome h1 span { color: #8d8d8d; }
  .welcome p {
    position: absolute; left: 23px; width: 690px; font-family: "Open Sans", Verdana, sans-serif;
    font-size: 13px; line-height: 22.5px; letter-spacing: 0.35px; color: var(--text-grey);
  }

  .footer {
    position: absolute; left: 0; top: 1166px; width: 1023px; height: 26px; color: #fff; font-size: 12.5px;
  }
  .footer .copyright { position: absolute; left: 40px; top: 4px; white-space: nowrap; }
  .footer nav { position: absolute; right: 33px; top: 4px; white-space: nowrap; }
  .footer nav a { color: #fff; text-decoration: none; }
  .footer nav .sep { margin: 0 6px; }
</style>
</head>
<body>
  <div class="page">
    <header>
      <div class="brand"><span class="brand-mark"></span><span class="brand-name">Dentist's Office</span></div>
      <div class="call-us">Call us: <span>000-000-0000</span></div>
    </header>

    <aside class="side-menu">
      <h3>Education</h3>
      <ul>
        <li>Emergency Dental Care</li><li>Your Mouth</li><li>Your Tooth</li><li>Cracked Tooth?</li>
        <li>Missing a Tooth?</li><li>Sensitive Teeth</li><li>Dry Mouth</li><li>Tooth Grinding</li><li>Sleep Dentistry</li>
      </ul>
      <h3>Preventative</h3>
      <ul>
        <li>What is Preventive Care?</li><li>Taking Care of Your Teeth</li><li>Eating Right</li><li>Dental Check-Ups</li>
        <li>Sealants</li><li>Periodontal Disease</li><li>Kicking the Habit</li><li>Night Gurards</li>
      </ul>
      <h3>Cosmetics</h3>
      <ul>
        <li>Cosmetic Dentistry</li><li>Bleaching and Whitening</li><li>Cosmetic Bonding</li><li>Esthetic Veneers</li><li>Tooth Shaping</li>
      </ul>
      <h3>Restorations</h3>
      <ul>
        <li>Crowns/Caps:Each Step</li><li>CMBRs</li><li>Porcelain Bridges</li><li>Bonded Dental Bridges</li><li>Gold Restorations</li><li>Implants</li>
      </ul>
      <h3>Visiting our office</h3>
      <ul>
        <li>Where to Stay</li><li>First Visit / Map</li><li>Financial Policy</li><li>Dental Insurance</li>
      </ul>
    </aside>
    <div class="divider"></div>

    <section class="side-box quick-contact">
      <h4 style="left:38px;top:9px;">Our Quick Contact</h4>
      <div class="picture" role="img" aria-label="Desk telephone" style="left:6px;top:30px;width:62px;height:56px;background:linear-gradient(#5b6a78,#2c3640);"></div>
      <div class="line" style="left:104px;top:44px;">Sample text</div>
      <div class="line" style="left:104px;top:64px;">Sample text</div>
      <div class="line" style="left:7px;top:98px;">Sample text here Sample text here</div>
      <div class="line" style="left:7px;top:118px;">Sample text here Sample text here</div>
    </section>

    <section class="side-box online-support">
      <h4 style="left:25px;top:9px;">24 Hours Online Support</h4>
      <div class="picture" role="img" aria-label="Portrait of a support assistant" style="left:15px;top:24px;width:66px;height:71px;background:linear-gradient(#f4f1ec,#d9c7b2);"></div>
      <div class="line" style="left:104px;top:44px;">Sample text</div>
      <div class="line" style="left:104px;top:64px;">Sample text</div>
      <div class="line" style="left:7px;top:98px;">Sample text here Sample text here</div>
      <div class="line" style="left:7px;top:118px;">Sample text here Sample text here</div>
    </section>

    <nav class="main-nav">
      <a href="#">Home</a><a href="#">Why we are Different</a><a href="#" class="active">Technologies we offer</a><a href="#">Meet Doctors</a><a href="#">Our Team</a><a href="#">Contact Us</a>
    </nav>

    <section class="hero">
      <div class="hero-photo" role="img" aria-label="Two smiling women side by side"></div>
      <div class="hero-question">Do you want a better looking Smile?</div>
      <div class="hero-visit">Visit our Office</div>
    </section>

    <main class="welcome">
      <h1><strong>Welcome to</strong> <span>Dentist office</span></h1>
      <p style="top:75px;">After 20 years of teaching dentists how to refine their technique and many years of writing textbooks, I currently devote my time to my office and the hands-on practice of dentistry. to welcome you personally to my dental practice, and I invite you to meet my highly experienced team of professionals.</p>
      <p style="top:214px;">We have offered complete dental care of the highest quality since 1978. We provide Preventive Services, Tooth Whitening and Cosmetic Dentistry for a beautiful smile,Endodontics (root canal treatment) to treat painful teeth, Sedation Dentistry so you can relax,and Dental Implants to restore what is missing.</p>
      <p style="top:282px;">We offer total care.</p>
      <p style="top:323px;">Our approach to your health is simple: We use our education, experience and dedication to provide every patient with superior dental care.</p>
      <p style="top:377px;">This passion for excellence is not just a goal, but a standard every member of our team holds.</p>
      <p style="top:408px;">We also pride ourselves with our state of the art procedures, training and technology. This includes creating a beautiful smile using techniques that preserve as much of the original tooth as possible.</p>
      <p style="top:472px;">Our abilities are renowned throughout the dental profession and I hope if you have any questions you will contact us by an e-mail note, by phone or just by dropping by.</p>
      <p style="top:528px;">We also pride ourselves with our state of the art procedures, training and technology. This includes creating a beautiful smile using techniques that preserve as much of the original tooth as possible.</p>
      <p style="top:587px;">We also pride ourselves with our state of the art procedures, training and technology. This includes creating a beautiful smile using techniques that preserve as much of the original tooth as possible.</p>
    </main>
  </div>

  <footer class="footer">
    <div class="copyright">copyright 2010 &nbsp;Dentist office All rights reserved.</div>
    <nav>
      <a href="#">Home</a><span class="sep">|</span><a href="#">Why we are Different</a><span class="sep">|</span><a href="#">Technologies we offer</a><span class="sep">|</span><a href="#">Meet Doctors</a><span class="sep">|</span><a href="#">Out Team</a><span class="sep">|</span><a href="#">Contact us</a>
    </nav>
  </footer>
</body>
</html>
```